Boutique custom software development company needs new business card

Our nearly 20 year old custom software development company would like to better include the fact that we are now providing Bitcoin services. These new services are B2B include education (how to acquire and securely hold Bitcoin) and integrating Bitcoin payments into existing ecommerce sites or other existing systems. Please keep the card clean and simple. Attached is our current design and some other files. vextorial.com

Target Market(s)

businesses owners interested in long term relationship

Industry/Entity Type

Custom software development and Bitcoin

Contact Information for Business Card

Dale Parker, dale@vextorial.com, vextorial.com, (888) 555-VXTRL

Font styles to use
Other font styles liked:
• monospace

Requirements
Must have
• double-sided
Nice to have
• clean and simple
Should not have
• physical address

```html
<!DOCTYPE html>
<html lang="en">
<head>
<meta charset="utf-8">
<title>Vextorial Business Card</title>
<link rel="stylesheet" href="https://fonts.googleapis.com/css2?family=Montserrat:wght@400;600;800&family=Open+Sans:wght@400;600&family=Courier+Prime:wght@700&display=swap">
<style>
  :root {
    --stage: #2b2b2b;
    --orange: #e8771f;
    --orange-deep: #d96c1a;
    --card-light: #efefef;
    --card-shade: #e3e3e3;
    --blue: #2f66ab;
    --ink: #3a3a3a;
    --white: #ffffff;
    --rule: #8a8a8a;
  }
  * { margin: 0; padding: 0; box-sizing: border-box; }
  html, body {
    width: 1200px; height: 900px; overflow: hidden;
    background: var(--stage);
  }
  .canvas {
    position: relative; width: 1200px; height: 900px;
    display: flex; flex-direction: column; align-items: center; justify-content: center; gap: 50px;
  }
  .card {
    position: relative; width: 560px; height: 320px; overflow: hidden;
    box-shadow: 0 10px 24px rgba(0,0,0,.45);
  }
  /* Front */
  .card-front {
    background: linear-gradient(135deg, var(--orange-deep) 0%, var(--orange) 70%);
    display: flex; flex-direction: column; align-items: center; justify-content: center;
  }
  .wordmark {
    font-family: "Montserrat", sans-serif; font-weight: 800;
    font-size: 60px; letter-spacing: 1px; color: var(--white); line-height: 1;
  }
  .tagline {
    margin-top: 10px; font-family: "Open Sans", sans-serif; font-size: 19px;
    color: var(--white); letter-spacing: -.2px;
  }
  .services {
    margin-top: 18px; padding-top: 10px; width: 360px;
    border-top: 1px solid rgba(255,255,255,.55);
    font-family: "Open Sans", sans-serif; font-weight: 600; font-size: 14px;
    color: var(--white); text-align: center; letter-spacing: .3px;
  }
  /* Back */
  .card-back {
    background: linear-gradient(120deg, var(--card-shade) 0%, var(--card-light) 55%, #f7f7f7 100%);
    display: flex; align-items: center;
  }
  .brand-block {
    width: 250px; height: 100%;
    display: flex; flex-direction: column; align-items: center; justify-content: center; gap: 14px;
  }
  .brand-name { display: flex; align-items: center; gap: 10px; }
  .brand-square { width: 34px; height: 34px; background: var(--blue); }
  .brand-text {
    font-family: "Montserrat", sans-serif; font-weight: 800; font-size: 30px; color: var(--blue);
  }
  .brand-url {
    font-family: "Courier Prime", monospace; font-weight: 700; font-size: 21px;
    color: var(--ink); letter-spacing: 2px;
  }
  .divider { width: 1px; height: 190px; background: var(--rule); }
  .contact { padding-left: 32px; }
  .contact-name {
    font-family: "Montserrat", sans-serif; font-weight: 800; font-size: 22px;
    color: var(--orange); letter-spacing: .5px; margin-bottom: 14px;
  }
  .contact-list { list-style: none; }
  .contact-item {
    display: flex; align-items: center; gap: 10px; margin-bottom: 8px;
    font-family: "Montserrat", sans-serif; font-size: 14px; color: var(--ink);
  }
  .contact-icon { width: 16px; height: 16px; flex: none; }
  .contact-services {
    margin-top: 14px; font-family: "Montserrat", sans-serif; font-weight: 600;
    font-size: 12px; line-height: 1.5; color: var(--blue);
  }
</style>
</head>
<body>
<main class="canvas">
  <section class="card card-front" aria-label="Card front">
    <div class="wordmark">VEXTORIAL</div>
    <div class="tagline">developer of custom applications</div>
    <div class="services">Bitcoin education &amp; payment integration</div>
  </section>

  <section class="card card-back" aria-label="Card back">
    <div class="brand-block">
      <div class="brand-name">
        <span class="brand-square"></span>
        <span class="brand-text">vextorial</span>
      </div>
      <div class="brand-url">vextorial.com</div>
    </div>
    <div class="divider"></div>
    <div class="contact">
      <div class="contact-name">DALE PARKER</div>
      <ul class="contact-list">
        <li class="contact-item">
          <svg class="contact-icon" viewBox="0 0 16 16" aria-hidden="true">
            <path d="M4 2 L6.5 2 L7.5 5 L6 6.3 C6.8 8 8 9.2 9.7 10 L11 8.5 L14 9.5 L14 12 C14 13 13 14 12 14 C6.5 13.6 2.4 9.5 2 4 C2 3 3 2 4 2 Z" fill="var(--blue)"/>
          </svg>
          (888) 555-VXTRL
        </li>
        <li class="contact-item">
          <svg class="contact-icon" viewBox="0 0 16 16" aria-hidden="true">
            <rect x="1.5" y="3.5" width="13" height="9" rx="1" fill="var(--blue)"/>
            <path d="M2 4.5 L8 9 L14 4.5" fill="none" stroke="var(--white)" stroke-width="1.3"/>
          </svg>
          dale@vextorial.com
        </li>
        <li class="contact-item">
          <svg class="contact-icon" viewBox="0 0 16 16" aria-hidden="true">
            <circle cx="8" cy="8" r="6.3" fill="none" stroke="var(--blue)" stroke-width="1.6"/>
            <ellipse cx="8" cy="8" rx="2.6" ry="6.3" fill="none" stroke="var(--blue)" stroke-width="1.2"/>
            <line x1="1.8" y1="8" x2="14.2" y2="8" stroke="var(--blue)" stroke-width="1.2"/>
          </svg>
          www.vextorial.com
        </li>
      </ul>
      <div class="contact-services">Custom software · Bitcoin services</div>
    </div>
  </section>
</main>
</body>
</html>
```